Brightway Haus Inc. Business Card Design

Brightway Haus Inc. is in search of a great clean design for our business cards!

Looking to incorporate our full logo and watermark on side one (however, I am open to having the text and watermark separated within the design.)

On side two, I am looking to have contact information (Name, Position, Phone #, Email, Website (www.thebrightwayhaus.ca). Can have the logo and/or watermark as part of the design if applicable.

Please add tagline "Where Shine Counts" on either side 1 or 2. This tagline can be in a sans serif, serif or cursive font as long as it compliments overall design. Capitalization can be title or sentence case depending on how it fits within the design.

Get creative!! Looking for a clean, crisp, premium design! Looking for a glossy card finish with spot UV features when printed. Cards will also be printed with rounded corners. Standard dimensions (3.5 x 2).

Target Market(s)

B2B - primary clients are business owners or property management corporations. (residential jobs are few and far between)

Industry/Entity Type

Business

Contact Information for Business Card

- clean, crisp design
- double sided
- spot UV accents and glossy finish upon printing
- standard business card size (3.5 x 2) with rounded corners
- please see project description for requirements per side

Font styles to use
Sans Serif

Requirements
Must have
• - adequate bleeds with print ready files
• - cohesive design elements between side 1 & 2
• - spot UV elements (can be on both sides or just one, use your discretion)
• - colour pallet should match the logo file provided
• - incorporate tagline "where shine counts" (this tagline can be in a serif or sans serif font as long as it is complimentary to the overall design.
Nice to have
• - Premium elements with a clean design
Should not have
• - Please omit cartoon or whimsical like designs, think premium.
• - Colours should not stray from the pallet of the provided logo.

```html
<!DOCTYPE html>
<html lang="en">
<head>
<meta charset="utf-8">
<title>Brightway Haus Inc. Business Card</title>
<link href="https://fonts.googleapis.com/css2?family=Open+Sans:wght@400;700&display=swap" rel="stylesheet">
<style>
  :root {
    --backdrop: #2b2b2b;
    --teal: #12b8b8;
    --navy: #1d2654;
    --white: #ffffff;
    --paper: #f1f1f1;
    --grey: #b3b3b3;
  }
  html, body {
    margin: 0;
    padding: 0;
    overflow: hidden;
  }
  body {
    width: 1200px;
    height: 960px;
    background: var(--backdrop);
    position: relative;
    font-family: "Open Sans", sans-serif;
  }
  .card {
    position: absolute;
    width: 600px;
    height: 343px;
    border-radius: 20px;
    overflow: hidden;
  }
  .card-front {
    left: 314px;
    top: 113px;
    background: var(--teal);
    color: var(--white);
  }
  .card-back {
    left: 311px;
    top: 472px;
    background: var(--paper);
  }
  .front-band {
    position: absolute;
    inset: 0;
  }
  .front-wordmark {
    position: absolute;
    left: 30px;
    top: 38px;
    margin: 0;
    font-size: 29px;
    font-weight: 700;
    letter-spacing: -0.5px;
  }
  .contact {
    position: absolute;
    left: 30px;
    top: 120px;
    font-size: 15px;
    line-height: 19px;
  }
  .contact-name {
    margin: 0;
    font-weight: 700;
    font-size: 15.5px;
  }
  .contact-role {
    margin: 0 0 9px;
    font-size: 15.5px;
  }
  .contact-address {
    margin: 0 0 4px;
    font-style: normal;
  }
  .contact-list {
    list-style: none;
    margin: 0;
    padding: 0;
  }
  .contact-list li {
    display: flex;
    align-items: center;
    gap: 9px;
    height: 19px;
  }
  .contact-list svg {
    width: 13px;
    height: 13px;
    flex: none;
  }
  .back-logo {
    position: absolute;
    left: 0;
    right: 0;
    top: 145px;
    display: flex;
    justify-content: center;
    align-items: center;
    gap: 12px;
  }
  .back-logo-mark {
    width: 40px;
    height: 40px;
    background: var(--teal);
  }
  .back-wordmark {
    margin: 0;
    font-size: 40px;
    font-weight: 700;
    color: var(--navy);
    letter-spacing: -1px;
    line-height: 1;
  }
  .tagline {
    position: absolute;
    left: 100px;
    right: 100px;
    top: 276px;
    display: flex;
    align-items: center;
    gap: 4px;
    margin: 0;
    font-size: 17px;
    font-weight: 700;
    color: var(--navy);
    white-space: nowrap;
  }
  .tagline::before,
  .tagline::after {
    content: "";
    flex: 1;
    height: 1px;
  }
  .tagline::before { background: linear-gradient(90deg, transparent, var(--navy)); }
  .tagline::after { background: linear-gradient(90deg, var(--navy), transparent); }
  .tagline-accent { color: var(--teal); }
</style>
</head>
<body>

<section class="card card-front" aria-label="Business card front">
  <svg class="front-band" viewBox="0 0 600 343" aria-hidden="true">
    <path d="M270 343 L288 298 Q420 232 600 168 L600 343 Z" fill="var(--navy)"/>
    <path d="M288 298 Q420 232 600 168 L600 180 Q430 242 292 306 Z" fill="var(--teal)"/>
  </svg>
  <h1 class="front-wordmark">BRIGHTWAY HAUS INC.</h1>
  <div class="contact">
    <p class="contact-name">MARA LINDQVIST</p>
    <p class="contact-role">CEO/FOUNDER</p>
    <address class="contact-address">214 Harbourview Road<br>Halifax, Nova Scotia B3H 1A1</address>
    <ul class="contact-list">
      <li>
        <svg viewBox="0 0 13 13" aria-label="Phone"><path d="M1 4 Q6.5 0 12 4 L10.5 5.5 L8.5 4.5 L8.5 3.5 Q6.5 2.8 4.5 3.5 L4.5 4.5 L2.5 5.5 Z M3 7 H10 L11 12 H2 Z" fill="var(--white)"/></svg>
        902 555 0148
      </li>
      <li>
        <svg viewBox="0 0 13 13" aria-label="Mobile"><rect x="3.5" y="0.5" width="6" height="12" rx="1" fill="none" stroke="var(--white)" stroke-width="1.5"/><rect x="5" y="2.5" width="3" height="6" fill="var(--white)"/></svg>
        902 555 0172
      </li>
      <li>
        <svg viewBox="0 0 13 13" aria-label="Fax"><rect x="3" y="1" width="7" height="4" fill="var(--white)"/><rect x="1" y="5.5" width="11" height="5" fill="var(--white)"/><rect x="3" y="9" width="7" height="3" fill="var(--white)"/></svg>
        902 555 0193
      </li>
      <li>
        <svg viewBox="0 0 13 13" aria-label="Email"><rect x="1" y="3" width="11" height="7" fill="var(--white)"/><path d="M1 3 L6.5 7 L12 3" fill="none" stroke="var(--teal)" stroke-width="1"/></svg>
        hello@brightwayhaus.ca
      </li>
      <li>
        <svg viewBox="0 0 13 13" aria-label="Website"><circle cx="6.5" cy="6.5" r="5.5" fill="var(--white)"/><path d="M4 4 Q6 5 5 7 Q7 8 8 10 M8 3 Q9 5 10 5" fill="none" stroke="var(--teal)" stroke-width="1"/></svg>
        www.thebrightwayhaus.ca
      </li>
    </ul>
  </div>
</section>

<section class="card card-back" aria-label="Business card back">
  <div class="back-logo">
    <span class="back-logo-mark" aria-hidden="true"></span>
    <h2 class="back-wordmark">BRIGHTWAY HAUS INC.</h2>
  </div>
  <p class="tagline">Where <span class="tagline-accent">&nbsp;Shine&nbsp;</span> Counts</p>
</section>

</body>
</html>
```